Book cover for book about Climate Change

Looking for a clean, bold, and attractive cover for a mass-market paperback (5.5"x 8.5") about solving the climate change problem. Title is either "Where the Rivers Meet” or A Harbor Made of Glass” (your choice), subtitle is "A practical field guide to mending the weather — so that the young ones after us inherit steady seasons and open skies," author is Lorne Whitcombe. Thinking that it *might* feature an image of Earth (or a portion thereof) and its very thin layer of atmosphere -- but STRONGLY encourage other ideas too!

Requirements
Nice to have
• Keep it positive — NOT scary doom-and-gloom

```html
<!DOCTYPE html>
<html lang="en">
<head>
<meta charset="utf-8">
<title>Where the Rivers Meet — Lorne Whitcombe</title>
<link rel="stylesheet" href="https://fonts.googleapis.com/css2?family=Poppins:wght@400;500;600;700;800&display=swap">
<style>
  :root {
    --backdrop: #a6a6a6;
    --paper: #ffffff;
    --leaf: #38a047;
    --leaf-light: #4cc565;
    --river: #3f9fc2;
    --ink: #1f1f1f;
    --sky: #dff1fb;
    --sea: #3d8fc4;
  }
  * { margin: 0; padding: 0; box-sizing: border-box; }
  html, body {
    width: 1200px;
    height: 1200px;
    overflow: hidden;
    background: var(--backdrop);
  }
  .cover {
    position: absolute;
    left: 247px;
    top: 54px;
    width: 706px;
    height: 1092px;
    background: var(--paper);
    overflow: hidden;
  }
  .title-art {
    position: absolute;
    left: 0;
    top: 0;
    width: 706px;
    height: 450px;
  }
  .title-art text {
    font-family: "Poppins", sans-serif;
    font-weight: 800;
  }
  .title-small { fill: var(--river); }
  .title-big { fill: var(--leaf); }
  .title-rule { stroke: var(--river); stroke-width: 2.5; }

  .subtitle {
    position: absolute;
    left: 63px;
    top: 445px;
    width: 580px;
    text-align: center;
    font-family: "Poppins", sans-serif;
    font-weight: 500;
    font-size: 21px;
    line-height: 31px;
    color: var(--ink);
  }
  .subtitle .lead {
    color: var(--leaf);
    font-weight: 600;
    text-transform: uppercase;
  }

  .scene {
    position: absolute;
    left: 110px;
    top: 551px;
    width: 463px;
    height: 445px;
    border-radius: 46% 46% 50% 50% / 38% 38% 62% 62%;
    background:
      radial-gradient(ellipse at 50% 22%, var(--sky) 0%, #cfe9d4 38%, transparent 60%),
      linear-gradient(180deg, #e6f4fb 0%, #9fd48a 45%, #5fbf62 62%, var(--sea) 82%, #2f7fa8 100%);
  }

  .author-band {
    position: absolute;
    left: 0;
    top: 1014px;
    width: 706px;
    height: 78px;
    background: linear-gradient(90deg, var(--leaf) 0%, var(--leaf-light) 100%);
    display: flex;
    align-items: center;
    justify-content: center;
  }
  .author-name {
    font-family: "Poppins", sans-serif;
    font-weight: 700;
    font-size: 35px;
    letter-spacing: 0.42em;
    margin-right: -0.42em;
    color: var(--paper);
    text-transform: uppercase;
  }
</style>
</head>
<body>
  <main class="cover">
    <svg class="title-art" viewBox="0 0 706 450" aria-labelledby="book-title">
      <title id="book-title">Where the Rivers Meet</title>
      <line class="title-rule" x1="87" y1="69" x2="212" y2="69"/>
      <line class="title-rule" x1="494" y1="69" x2="618" y2="69"/>
      <text class="title-small" x="223" y="88" font-size="50" textLength="260" lengthAdjust="spacingAndGlyphs">WHERE THE</text>
      <text class="title-big" x="87" y="262" font-size="180" textLength="531" lengthAdjust="spacingAndGlyphs">RIVERS</text>
      <text class="title-big" x="87" y="436" font-size="200" textLength="531" lengthAdjust="spacingAndGlyphs">MEET</text>
    </svg>

    <p class="subtitle"><span class="lead">A practical field guide</span> to mending the weather — so that the young ones after us inherit steady seasons and open skies</p>

    <div class="scene" role="img" aria-label="Illustration of people planting and recycling among wind turbines, solar panels and trees on top of a half globe of the Earth"></div>

    <footer class="author-band">
      <span class="author-name">Lorne Whitcombe</span>
    </footer>
  </main>
</body>
</html>
```